Agriculture Business Card

I want to use my existing logo and use my tagline of "Don't Guess...Soil Test" on the card. Looking for a double sided card that will really get peoples attention.
Contact Info:
Marlow Field Crop Edge
Calvin Brusk
2917 K Lane
Larkin, NE 68593
402-555-0193
calvin.r.brusk@fieldmailbox.net

```html
<!DOCTYPE html>
<html lang="en">
<head>
<meta charset="utf-8">
<title>Marlow Field Crop Edge – Business Card</title>
<link rel="stylesheet" href="https://fonts.googleapis.com/css2?family=Arimo:wght@400;700&display=swap">
<style>
  :root {
    --backdrop: #e4e4e4;
    --card: #ffffff;
    --brown: #9a5a3c;
    --ink: #3a3a3a;
    --rule: #777777;
    --gold: #f9b21d;
    --leaf: #6dbd45;
    --leaf-pale: #e3efdc;
    --gold-pale: #fdefd6;
  }
  * { margin: 0; padding: 0; box-sizing: border-box; }
  html, body {
    width: 1200px; height: 1200px; overflow: hidden;
    background: var(--backdrop);
    font-family: "Arimo", Arial, sans-serif;
  }
  .card {
    position: absolute; left: 253px; width: 730px; height: 428px;
    background: var(--card); overflow: hidden;
    box-shadow: 0 1px 4px rgba(0, 0, 0, 0.25);
  }
  .card--front { top: 135px; }
  .card--back { top: 600px; }

  .edge-band {
    position: absolute; right: 0; top: 0; width: 250px; height: 100%;
    background: linear-gradient(90deg, rgba(255,255,255,0) 0%, var(--gold-pale) 55%, var(--leaf-pale) 100%);
  }

  .brand-block {
    position: absolute; left: 30px; top: 40px; width: 185px;
    display: flex; flex-direction: column; align-items: center; gap: 12px;
  }
  .brand-dot { width: 96px; height: 96px; border-radius: 50%; background: var(--gold); }
  .brand-name {
    color: var(--brown); font-weight: 700; font-size: 22px;
    line-height: 24px; text-align: center;
  }

  .tagline {
    color: var(--leaf); font-weight: 700; white-space: nowrap;
  }
  .tagline--front {
    position: absolute; right: 40px; top: 274px; font-size: 18px;
  }

  .holder-name {
    position: absolute; left: 44px; top: 268px;
    color: var(--brown); font-size: 24px; font-weight: 400;
  }
  .holder-rule {
    position: absolute; left: 44px; top: 300px; width: 646px; height: 1px;
    background: var(--rule);
  }
  .contact {
    position: absolute; left: 44px; top: 309px;
    list-style: none; color: var(--ink); font-size: 17px; line-height: 22px;
  }
  .contact li { display: flex; align-items: center; gap: 7px; }
  .contact svg { width: 13px; height: 13px; fill: var(--gold); }
  .address {
    position: absolute; left: 46px; top: 368px;
    color: var(--ink); font-size: 17px;
  }
  .address .company { color: var(--brown); }

  .back-mark {
    position: absolute; left: 70px; top: 110px;
    width: 190px; height: 190px; border-radius: 50%; background: var(--gold);
  }
  .back-text {
    position: absolute; left: 290px; top: 150px; width: 380px;
    display: flex; flex-direction: column; align-items: center; gap: 18px;
  }
  .back-name {
    color: var(--brown); font-weight: 700; font-size: 46px;
    line-height: 54px; text-align: center;
  }
  .tagline--back { font-size: 22px; }
</style>
</head>
<body>
  <section class="card card--front">
    <div class="edge-band" aria-hidden="true"></div>
    <div class="brand-block">
      <span class="brand-dot"></span>
      <span class="brand-name">Marlow Field<br>Crop Edge</span>
    </div>
    <p class="tagline tagline--front">Don't Guess...Soil Test</p>
    <h1 class="holder-name">Calvin Brusk</h1>
    <div class="holder-rule"></div>
    <ul class="contact">
      <li>
        <svg viewBox="0 0 24 24" aria-hidden="true"><path d="M6.6 10.8a15.1 15.1 0 0 0 6.6 6.6l2.2-2.2a1 1 0 0 1 1-.25 11.4 11.4 0 0 0 3.6.57 1 1 0 0 1 1 1V20a1 1 0 0 1-1 1A17 17 0 0 1 3 4a1 1 0 0 1 1-1h3.5a1 1 0 0 1 1 1c0 1.25.2 2.45.57 3.57a1 1 0 0 1-.25 1z"/></svg>
        402-555-0193
      </li>
      <li>
        <svg viewBox="0 0 24 24" aria-hidden="true"><path d="M2 5h20v14H2z M2 5l10 8 10-8" stroke="#fff" stroke-width="1.5"/></svg>
        calvin.r.brusk@fieldmailbox.net
      </li>
    </ul>
    <p class="address"><span class="company">Marlow Field Crop Edge:</span> 2917 K Lane, Larkin, NE 68593</p>
  </section>

  <section class="card card--back">
    <span class="back-mark"></span>
    <div class="back-text">
      <p class="back-name">Marlow Field<br>Crop Edge</p>
      <p class="tagline tagline--back">Don't Guess...Soil Test</p>
    </div>
  </section>
</body>
</html>
```